Salon and Spa Distributor Business Card

Need a business card. We are are distributor in the salon and spa industry. We identify with natural beauty. Need a card with:
Company Name: Petal Quarry"
Title: "President & CEO"
Address
Company Phone number
email
website
Tag Line:" The Professional Salon Source"

Industry/Entity Type

Business

Contact Information for Business Card

Name: Dov Strommen
Title: "President & CEO"
Address: 31 Harlow Ln, Bexmoor, NJ 07813
Company Phone number: 800-463-5918
email: dovstrommen@petalquarry.example
website: www.petalquarry.example

Requirements
Should not have
• No black backgrounds

```html
<!DOCTYPE html>
<html lang="en">
<head>
<meta charset="utf-8">
<title>Petal Quarry — Business Card</title>
<link href="https://fonts.googleapis.com/css2?family=Mulish:wght@400;700&display=swap" rel="stylesheet">
<style>
  :root {
    --page-bg: #e8e3db;
    --card-bg: #eef1ee;
    --card-edge: #d7dbd6;
    --brand-green: #2f8f2c;
    --name-green: #1e6a29;
    --ink: #3a3d3a;
    --icon-green: #2a6b31;
  }
  * { margin: 0; padding: 0; box-sizing: border-box; }
  html, body {
    width: 1200px; height: 1010px; overflow: hidden;
    background: var(--page-bg);
    font-family: "Mulish", "Century Gothic", sans-serif;
  }
  .card {
    position: absolute; left: 100px; top: 215px;
    width: 1000px; height: 580px;
    background: var(--card-bg);
    border: 1px solid var(--card-edge);
    box-shadow: 0 18px 40px rgba(60, 50, 40, 0.18);
  }
  .brand-dot {
    position: absolute; left: 38px; top: 96px;
    width: 140px; height: 140px; border-radius: 50%;
    background: var(--brand-green);
  }
  .brand-name {
    position: absolute; left: 220px; top: 100px;
    font-size: 46px; font-weight: 400; line-height: 1;
    color: var(--brand-green);
  }
  .tagline {
    position: absolute; left: 227px; top: 170px;
    font-size: 23px; color: var(--ink); line-height: 1;
  }
  .person { position: absolute; left: 61px; top: 438px; }
  .person-name {
    font-size: 36px; font-weight: 700; color: var(--name-green); line-height: 1;
  }
  .person-title {
    margin-top: 14px; font-size: 21px; color: var(--ink); line-height: 1;
  }
  .contacts {
    position: absolute; left: 490px; top: 366px; list-style: none;
  }
  .contact {
    display: flex; align-items: center; height: 35.5px;
    font-size: 24px; color: var(--ink);
  }
  .contact svg { width: 24px; height: 24px; margin-right: 18px; fill: var(--icon-green); }
  .address {
    position: absolute; left: 483px; top: 480px;
    font-size: 24px; color: var(--ink); line-height: 1;
  }
</style>
</head>
<body>
  <section class="card">
    <div class="brand-dot"></div>
    <div class="brand-name">Petal Quarry</div>
    <div class="tagline">The Professional Salon Source</div>

    <div class="person">
      <div class="person-name">Petal Quarry</div>
      <div class="person-title">President &amp; CEO</div>
    </div>

    <ul class="contacts">
      <li class="contact">
        <svg viewBox="0 0 24 24" aria-hidden="true"><path d="M3 8c0-2 4-4 9-4s9 2 9 4v2h-5V8.5c-1-.6-2.5-.9-4-.9s-3 .3-4 .9V10H3z"/><path d="M7 11h10l3 8H4z"/><circle cx="12" cy="15" r="2" fill="#eef1ee"/></svg>
        800-463-5918
      </li>
      <li class="contact">
        <svg viewBox="0 0 24 24" aria-hidden="true"><path d="M2 5h20v14H2z"/><path d="M2.5 5.5l9.5 7.5 9.5-7.5" stroke="#eef1ee" stroke-width="1.8" fill="none"/></svg>
        dovstrommen@petalquarry.example
      </li>
      <li class="contact">
        <svg viewBox="0 0 24 24" aria-hidden="true"><circle cx="12" cy="12" r="10"/><g stroke="#eef1ee" stroke-width="1.4" fill="none"><ellipse cx="12" cy="12" rx="4" ry="10"/><path d="M2 12h20M4 7h16M4 17h16"/></g></svg>
        www.petalquarry.example
      </li>
    </ul>

    <div class="address">31 Harlow Ln, Bexmoor, NJ 07813</div>
  </section>
</body>
</html>
```